Brave Lotus - Fitness Retreat

Tri Fold Brochure & Double sided A4 version options, see attached mockup.

Target Market: Women 18-50, Asian mainly .

Kelvar Fitness Presents - Brave Lotus Fitness Retreats:

Something communicating the spirit of getting fit, being strong, eating healthy and strong sense of the feminine.

Industry/Entity Type

Fitness

```html
<!DOCTYPE html>
<html lang="en">
<head>
<meta charset="utf-8">
<title>Brave Lotus – Boot Camp Bali Retreats</title>
<link rel="stylesheet" href="https://fonts.googleapis.com/css2?family=Archivo+Black&family=Noto+Serif:ital,wght@0,400;0,700;1,400;1,700&family=Open+Sans:wght@400;700&display=swap">
<style>
:root{
  --red:#c8202a;
  --red-dark:#9e1219;
  --red-deep:#7d0d12;
  --yellow:#ffd23f;
  --gold:#f6b400;
  --cream:#fff6e8;
  --ink:#3a2a2a;
  --grey-bg:#e9e9e9;
  --white:#ffffff;
  --pale-red:#f3d7d7;
}
*{box-sizing:border-box;margin:0;padding:0}
html,body{width:1200px;height:1115px;overflow:hidden;background:var(--grey-bg)}
body{position:relative;font-family:"Noto Serif",serif;color:var(--ink)}
.sheet{position:absolute;top:150px;width:570px;height:806px;background:var(--white);box-shadow:0 2px 10px rgba(0,0,0,.18);overflow:hidden}
.sheet--back{left:20px}
.sheet--front{left:610px;background:linear-gradient(160deg,#d9302f 0%,var(--red) 45%,var(--red-dark) 100%)}

/* back sheet */
.info-column{position:absolute;left:0;top:0;width:250px;height:100%;background:linear-gradient(170deg,var(--red) 0%,var(--red-dark) 70%,var(--red-deep) 100%);padding:20px 16px;color:var(--white);font-family:"Open Sans",sans-serif}
.info-block{margin-bottom:7px}
.info-block h3{font-size:8.5px;color:var(--yellow);text-transform:uppercase;font-weight:700;letter-spacing:.2px;margin-bottom:1px}
.info-block p{font-size:6.2px;line-height:1.35;color:#ffe9c9}
.info-column .hints-title{font-size:9px;color:var(--white);text-align:center;font-weight:700;margin:6px 0 6px}
.terms-column{position:absolute;left:266px;top:18px;width:290px;font-family:"Open Sans",sans-serif}
.terms-column h3{font-size:8.5px;color:var(--red);font-weight:700;text-transform:uppercase;margin-bottom:2px}
.terms-column h3.terms-title{color:var(--ink);font-size:9.5px;margin-top:6px}
.terms-column p{font-size:6.2px;line-height:1.4;margin-bottom:6px}
.terms-list{list-style:none;font-size:6.2px;line-height:1.4}
.terms-list li{position:relative;padding-left:9px;margin-bottom:3px}
.terms-list li::before{content:"";position:absolute;left:1px;top:3px;width:4px;height:4px;border-radius:50%;background:var(--red)}
.photo-strip{position:absolute;left:266px;top:396px;width:84px}
.photo{height:50px;margin-bottom:6px;border-radius:2px;background:linear-gradient(135deg,#8fbf6c,#d9c9a6 60%,#b9d3e6)}
.photo:nth-child(2n){background:linear-gradient(135deg,#c9dbe8,#e6c9b0 55%,#8fae6e)}
.schedule{position:absolute;left:360px;top:396px;width:198px;font-family:"Open Sans",sans-serif}
.schedule h4{font-family:"Noto Serif",serif;font-style:italic;font-weight:700;color:var(--red);font-size:11px;margin-bottom:3px}
.schedule table{width:100%;border-collapse:collapse;font-size:5.4px}
.schedule th{background:var(--red);color:var(--white);padding:3px;text-align:left;font-size:6px}
.schedule td{border-bottom:1px solid var(--pale-red);padding:2px 3px;vertical-align:middle}
.schedule td.day{width:34px;font-weight:700;font-size:7px;text-align:center;background:#fbeeee;color:var(--ink)}
.schedule .time{color:var(--red);font-weight:700;width:22px}

/* front sheet */
.brand-mark{position:absolute;left:0;right:0;top:40px;text-align:center;font-family:"Noto Serif",serif;font-weight:700;font-size:14px;color:var(--white);letter-spacing:1px}
.brand-mark .square{display:inline-block;width:16px;height:16px;background:var(--white);vertical-align:-2px;margin-right:6px}
.title{position:absolute;left:0;right:0;top:96px;text-align:center;font-family:"Archivo Black",sans-serif;font-size:36px;color:var(--white);letter-spacing:1px}
.subtitle{position:absolute;left:0;right:0;top:150px;text-align:center;font-family:"Open Sans",sans-serif;font-weight:700;font-size:10px;letter-spacing:1.5px;color:#3a0d0d}
.tagline{position:absolute;left:20px;top:184px;width:200px;text-align:center;font-weight:700;font-size:14.5px;line-height:1.35;color:var(--cream)}
.price{position:absolute;left:214px;top:186px;width:56px;height:56px;border-radius:50%;background:var(--white);border:3px solid var(--red-dark);text-align:center;font-weight:700;color:var(--red);line-height:1}
.price .amount{display:block;font-size:15px;margin-top:14px}
.price .cur{position:absolute;left:8px;top:4px;font-size:11px}
.price .pp{font-size:9px}
.photo-hero{position:absolute;right:0;top:170px;width:260px;height:460px;background:linear-gradient(180deg,rgba(120,40,30,.0),rgba(150,60,45,.35) 30%,rgba(180,100,70,.45) 60%,rgba(120,30,30,.2))}
.lists{position:absolute;left:20px;top:262px;width:250px;font-family:"Open Sans",sans-serif}
.lists h3{font-size:9px;color:var(--yellow);font-weight:700;text-transform:uppercase;margin-bottom:4px}
.lists ul{list-style:none;font-size:6.4px;color:var(--gold);margin-bottom:12px}
.lists li{position:relative;padding-left:8px;margin-bottom:4px;line-height:1.3}
.lists li::before{content:"";position:absolute;left:0;top:2px;width:3.5px;height:3.5px;background:var(--yellow)}
.banner{position:absolute;left:0;right:0;top:512px;height:44px;background:rgba(205,185,220,.55);text-align:center;padding-top:7px;font-style:italic;font-weight:700;font-size:9.5px;line-height:1.5;color:#3a1c5a}
.footer-wave{position:absolute;left:0;bottom:0;width:570px;height:240px}
.footer-brand{position:absolute;left:40px;top:636px;width:210px;text-align:center}
.footer-brand .square{display:inline-block;width:22px;height:22px;background:var(--red);margin-bottom:8px}
.footer-brand .name{font-family:"Archivo Black",sans-serif;font-size:22px;color:var(--red);letter-spacing:.5px}
.footer-brand .sub{font-family:"Open Sans",sans-serif;font-size:9px;color:var(--ink);letter-spacing:1.5px;margin-top:2px}
.contacts{position:absolute;left:300px;top:660px;width:250px;font-size:8.5px;color:var(--red);line-height:1.4}
.contact-group{display:flex;gap:10px;margin-bottom:14px;align-items:flex-start}
.contact-group .square{flex:none;width:16px;height:16px;background:var(--red);margin-top:3px}
.contact-group .circle{flex:none;width:16px;height:16px;border-radius:50%;border:1.5px solid var(--ink);margin-top:3px}
</style>
</head>
<body>

<section class="sheet sheet--back" aria-label="Brochure back">
  <div class="info-column">
    <div class="info-block"><h3>Training Sessions</h3><p>Every session suits all levels. Trainers adapt each drill so you can go at your pace and still feel the burn.</p></div>
    <div class="info-block"><h3>Yoga &amp; Stretch Sessions</h3><p>Calm morning flows and gentle stretch to help the body recover.</p></div>
    <div class="info-block"><h3>Walks &amp; Treks</h3><p>Guided walks through rice fields and villages, with water and snacks along the way.</p></div>
    <div class="info-block"><h3>Shoes</h3><p>Bring good trainers for sessions and a pair of sandals for downtime.</p></div>
    <div class="info-block"><h3>Everyday</h3><p>Pack light clothes, a hat, sunscreen, swimwear and a small daypack. Laundry is easy to find close to the retreat and is cheap to use.</p></div>
    <div class="info-block"><h3>Banned Narcotics</h3><p>Drugs of any kind are strictly banned and carry heavy penalties.</p></div>
    <div class="info-block"><h3>Bits &amp; Pieces</h3><p>Bring a water bottle, insect spray, any medicines you need and a light jacket for cool evenings in the hills.</p></div>
    <div class="info-block"><h3>Volcano / Hot Springs</h3><p>The sunrise climb starts early. Warm layers and a torch are useful, and a soak in the springs follows the descent.</p></div>
    <div class="info-block"><h3>Group Transfers</h3><p>Transfers run from the airport or a nearby hotel on day one and return on day six.</p></div>
    <div class="info-block"><h3>Safety</h3><p>Travel insurance is required. Please share any health issues with your trainer before the first session.</p></div>
    <div class="hints-title">HANDY TRAVEL HINTS</div>
    <div class="info-block"><h3>Air Port (International)</h3><p>Allow time for the arrival queue. Keep your passport, return ticket and retreat address close at hand, and use only official taxi desks if travelling alone.</p></div>
    <div class="info-block"><h3>Staying in Touch</h3><p>Local SIM cards are cheap at the airport. Wi-Fi is available at the retreat in common areas, though signal may drop in the hills.</p></div>
    <div class="info-block"><h3>Drinking Water</h3><p>Drink only bottled or filtered water, including for brushing teeth.</p></div>
    <div class="info-block"><h3>Money</h3><p>Local currency is rupiah. Use bank ATMs and carry small notes for markets.</p></div>
  </div>

  <div class="terms-column">
    <h3>Meals</h3>
    <p>Meals are a shared, social time. Expect fresh local dishes, fruit, salads and lean protein served three times a day. Tell us about any dietary needs before arrival so our kitchen can prepare for you.</p>
    <h3>Alcohol</h3>
    <p>The only alcohol we serve is one local beer at the farewell dinner. Bring your own water bottle and stay hydrated.</p>
    <h3 class="terms-title">Terms &amp; Conditions</h3>
    <ul class="terms-list">
      <li>Travel insurance is mandatory for all of our guests.</li>
      <li>Please confirm any special dietary needs before booking so we can plan meals for the group.</li>
      <li>All guests must complete a Fitness &amp; Health Assessment before the retreat starts.</li>
      <li>Instalment payment is possible to secure your place with a non-refundable deposit.</li>
      <li>Final payment must be made 30 days prior to arrival.</li>
      <li>Refunds are not given once the retreat has started.</li>
      <li>Refunds will not be given for missed sessions or activities during the week.</li>
      <li>Personal expenses will be paid on checkout at the retreat.</li>
      <li>We operate rain, hail or shine!</li>
    </ul>
  </div>

  <div class="photo-strip">
    <div class="photo" role="img" aria-label="Retreat guests boxing outdoors"></div>
    <div class="photo" role="img" aria-label="Group stretching on grass"></div>
    <div class="photo" role="img" aria-label="Guests training on a lawn"></div>
    <div class="photo" role="img" aria-label="Beach workout"></div>
    <div class="photo" role="img" aria-label="Partner exercises on the grass"></div>
    <div class="photo" role="img" aria-label="Tyre training on the beach"></div>
    <div class="photo" role="img" aria-label="Group circuit on sand"></div>
  </div>

  <div class="schedule">
    <h4>BRAVE LOTUS SCHEDULE</h4>
    <table>
      <tr><th>DAYS</th><th colspan="2">ACTIVITIES</th></tr>
      <tr><td class="day" rowspan="3">ONE</td><td class="time">1pm</td><td>Arrival &amp; transfer</td></tr>
      <tr><td class="time">4pm</td><td>Welcome &amp; fitness check</td></tr>
      <tr><td class="time">7pm</td><td>Welcome dinner</td></tr>
      <tr><td class="day" rowspan="4">TWO</td><td class="time">6am</td><td>Sunrise yoga</td></tr>
      <tr><td class="time">9am</td><td>Boxing circuit</td></tr>
      <tr><td class="time">2pm</td><td>Rice field walk</td></tr>
      <tr><td class="time">7pm</td><td>Dinner</td></tr>
      <tr><td class="day" rowspan="4">THREE</td><td class="time">6am</td><td>Beach boot camp</td></tr>
      <tr><td class="time">12pm</td><td>Lunch</td></tr>
      <tr><td class="time">3pm</td><td>Stretch &amp; recover</td></tr>
      <tr><td class="time">7pm</td><td>Dinner</td></tr>
      <tr><td class="day" rowspan="4">FOUR</td><td class="time">2am</td><td>Volcano sunrise trek</td></tr>
      <tr><td class="time">12pm</td><td>Lunch</td></tr>
      <tr><td class="time">2pm</td><td>Hot springs soak</td></tr>
      <tr><td class="time">7pm</td><td>Dinner</td></tr>
      <tr><td class="day" rowspan="4">FIVE</td><td class="time">6am</td><td>Strength &amp; conditioning</td></tr>
      <tr><td class="time">9am</td><td>Breakfast</td></tr>
      <tr><td class="time">3pm</td><td>Massage</td></tr>
      <tr><td class="time">7pm</td><td>Farewell dinner &amp; dance</td></tr>
      <tr><td class="day" rowspan="3">SIX</td><td class="time">6am</td><td>Final training &amp; yoga</td></tr>
      <tr><td class="time">9am</td><td>Breakfast</td></tr>
      <tr><td class="time">11am</td><td>Transfer out</td></tr>
    </table>
  </div>
</section>

<section class="sheet sheet--front" aria-label="Brochure front">
  <div class="brand-mark"><span class="square"></span>Kelvar Fitness</div>
  <h1 class="title">BRAVE LOTUS</h1>
  <div class="subtitle">BOOT CAMP BALI RETREATS</div>
  <p class="tagline">6 Days/ 5 Nights<br>Fitness, Fun,<br>Friendship &amp; Adventure</p>
  <div class="price"><span class="cur">$</span><span class="amount">1650</span><span class="pp">pp</span></div>

  <div class="photo-hero" role="img" aria-label="Athletic woman in sportswear standing with hands on hips"></div>

  <div class="lists">
    <h3>Inclusions</h3>
    <ul>
      <li>Food and Accommodation.</li>
      <li>Group transfers from airport or nearby hotel to retreat on Day 1.</li>
      <li>Group transfers to airport or nearby hotel from retreat on Day 6.</li>
      <li>All activities on the program.</li>
      <li>Bonus Gift.</li>
      <li>Pair of Boxing Gloves.</li>
      <li>Brave Lotus Tank Top &amp; Workout Towel.</li>
      <li>60 min Massage.</li>
    </ul>
    <h3>Exclusions</h3>
    <ul>
      <li>Flights to/from Bali.</li>
      <li>Travel insurance.</li>
      <li>Bottled drinks such as water, soft drinks, beer.</li>
      <li>Personal laundry.</li>
      <li>Extra tours, transport, massages, spa treatments outside the program.</li>
    </ul>
  </div>

  <div class="banner">Be prepared to challenge yourself and have a lot of fun.<br>Most importantly pack an open mind! You are about to have a very unique experience.</div>

  <svg class="footer-wave" viewBox="0 0 570 240" aria-hidden="true">
    <path d="M0 20 C120 80 260 50 380 36 C460 26 530 14 570 0 L570 240 L0 240 Z" fill="#ffffff"/>
  </svg>

  <div class="footer-brand">
    <span class="square"></span>
    <div class="name">BRAVE LOTUS</div>
    <div class="sub">BOOT CAMP BALI RETREATS</div>
  </div>

  <div class="contacts">
    <div class="contact-group"><span class="square"></span><div>mara@kelvarfitness.example<br>+62 812.0000.4182<br>www.kelvarfitness.example</div></div>
    <div class="contact-group"><span class="circle"></span><div>hello@islandshare.example<br>+62 812.0000.7265<br>www.islandshare.example</div></div>
  </div>
</section>

</body>
</html>
```